The Marigold Venture WEBSITE DESIGN

Marigold is a not for profit working in international aid and development. The website needs to be lively not depressing,earthy rather than bling, have a dramatic impact over lightweight. It may be that a black and white with spot colour may be more impacting given the simplicity I want for the site. Marigold works in partnership with registered NGOs in Asia and Africa. At any one time it will have about five feature projects. The purpose is for people to be able to find out about the projects, the countries, the partner organisations, people's stories and then give people the opportunity to give their financial and volunteer support.

Target Market(s)

First World Donors
All ages but particularly 25 - 55

Industry/Entity Type

Human Rights

Number of Pages Required

5+ page

Font styles to use
Sans Serif

Requirements
Must have
• Simplicity
• Easy access to giving options
• Highlight stories both video and image + copy (sample in attachments)
• Lots of images over copy
Nice to have
• Interest
• Not boring
• May work in black and white with a spot colour or sepia look
Should not have
• Shiny new look
• Dont know how many pages or if it be coded or uncoded - makes no sense to me

```html
<!DOCTYPE html>
<html lang="en">
<head>
<meta charset="utf-8">
<title>The Marigold Venture</title>
<link rel="stylesheet" href="https://fonts.googleapis.com/css2?family=Open+Sans:wght@400;600;700&family=Oswald:wght@400;500&display=swap">
<style>
:root{
  --spot:#e58a2a;
  --ink:#333333;
  --muted:#777777;
  --line:#e2e2e2;
  --sepia-dark:#3a2f27;
  --sepia-mid:#7a6450;
  --sepia-light:#b59b7e;
  --icon:#6f6f6f;
  --footer:#3b3b3b;
  --footer-base:#262626;
  --white:#ffffff;
}
*{box-sizing:border-box;margin:0;padding:0}
html,body{width:1200px;height:2592px;overflow:hidden;background:var(--white)}
body{position:relative;font-family:"Open Sans",Arial,sans-serif;color:var(--ink)}
.abs{position:absolute}
.photo{position:absolute;background:linear-gradient(135deg,var(--sepia-light),var(--sepia-mid) 55%,var(--sepia-dark))}

/* header */
.brand{left:100px;top:22px;display:flex;align-items:center;gap:10px}
.brand-dot{width:40px;height:40px;border-radius:50%;background:var(--spot)}
.brand-name{font-weight:700;font-size:22px;color:var(--spot);line-height:1}
.contact-bar{right:100px;top:40px;display:flex;align-items:center;gap:10px;font-size:17px;color:var(--ink)}
.phone-icon{width:34px;height:34px;border:2px solid var(--ink);border-radius:50%;display:flex;align-items:center;justify-content:center;margin-right:6px}
.social{width:28px;height:28px;border:2px solid var(--muted);border-radius:50%}
.nav{right:100px;top:112px;display:flex;gap:28px;font-size:13px;font-weight:600;text-transform:uppercase;color:var(--ink)}
.nav .active{color:var(--muted)}

/* hero */
.hero{left:0;top:160px;width:1200px;height:552px}
.hero-title{left:100px;top:470px;font-family:"Oswald",sans-serif;font-size:44px;font-weight:500;color:var(--white);letter-spacing:1px}
.hero-sub{left:100px;top:528px;font-size:28px;color:var(--white)}
.hero-arrow{top:416px;width:32px;height:40px;background:rgba(0,0,0,.45);display:flex;align-items:center;justify-content:center}

/* section titles */
.section-title{width:1200px;left:0;text-align:center;font-size:28px;font-weight:600;text-transform:uppercase;color:var(--ink)}
.section-title span{color:var(--spot)}
.section-title.light{color:var(--white)}
.intro{left:200px;width:800px;text-align:center;font-size:13px;line-height:20px;color:var(--muted)}

/* about features */
.feature{top:880px;width:200px;text-align:center}
.feature-icon{width:92px;height:92px;margin:0 auto;border-radius:50%;background:var(--icon);display:flex;align-items:center;justify-content:center}
.feature h3{margin-top:26px;font-size:15px;font-weight:700;text-transform:uppercase}
.feature p{margin-top:10px;font-size:12px;line-height:18px;color:var(--muted)}

/* projects */
.projects{left:0;top:1140px;width:1200px;height:440px;background:linear-gradient(180deg,#4a3d33,var(--sepia-dark))}
.project{top:1272px;width:320px}
.project .photo{position:relative;width:320px;height:188px;border:6px solid var(--white)}
.project h4{margin-top:18px;font-size:15px;font-weight:600;color:var(--white)}
.project p{margin-top:6px;font-size:12px;line-height:18px;color:#d8cdc2}

/* news */
.video{left:100px;top:1788px;width:480px;height:280px}
.play{left:310px;top:1898px;width:60px;height:60px;border-radius:50%;background:rgba(255,255,255,.85);display:flex;align-items:center;justify-content:center}
.story-title{left:612px;top:1972px;font-size:17px;font-weight:600}
.story-text{left:612px;top:2004px;width:496px;font-size:12px;line-height:18px;color:var(--muted)}

/* giving */
.give{top:2140px;height:148px}
.give-label{position:absolute;left:0;bottom:0;width:100%;height:64px;background:rgba(30,24,20,.55);color:var(--white);font-size:30px;padding:10px 36px}

/* footer */
.footer{left:0;top:2320px;width:1200px;height:208px;background:var(--footer)}
.footer-col{top:2340px;width:230px;color:#c9c9c9;font-size:11px;line-height:18px}
.footer-col h5{color:var(--white);font-size:13px;font-weight:700;text-transform:uppercase;margin-bottom:12px}
.footer-col li{list-style:none}
.footer-col li::before{content:"› ";color:var(--spot)}
.signup{display:flex;margin-top:10px}
.signup span{display:block;width:150px;height:28px;background:var(--white);color:var(--muted);padding:5px 8px}
.signup b{display:block;height:28px;background:#111;color:var(--white);padding:5px 10px;font-weight:600}
.footer-social{display:flex;gap:10px;margin-top:16px;margin-left:40px}
.footer-social i{width:26px;height:26px;border:2px solid #bbb;border-radius:50%}
.base{left:0;top:2528px;width:1200px;height:64px;background:var(--footer-base);color:#bbb;font-size:11px;text-align:center;line-height:64px}
</style>
</head>
<body>

<header>
  <div class="abs brand"><span class="brand-dot"></span><span class="brand-name">Marigold</span></div>
  <div class="abs contact-bar">
    <span class="phone-icon"><svg width="16" height="16" viewBox="0 0 24 24"><path d="M6.6 10.8a15 15 0 006.6 6.6l2.2-2.2c.3-.3.7-.4 1-.2 1.1.4 2.3.6 3.6.6.6 0 1 .4 1 1V20c0 .6-.4 1-1 1A17 17 0 013 4c0-.6.4-1 1-1h3.5c.6 0 1 .4 1 1 0 1.3.2 2.5.6 3.6.1.3 0 .7-.2 1z" fill="#333"/></svg></span>
    <span>555-014-2290</span>
    <span style="width:14px"></span>
    <i class="social"></i><i class="social"></i><i class="social"></i><i class="social"></i>
  </div>
  <nav class="abs nav">
    <span class="active">Home</span><span>About Marigold</span><span>Current Projects</span><span>News/Stories</span><span>Giving</span><span>Contact</span>
  </nav>
</header>

<section>
  <div class="photo hero" role="img" aria-label="Sepia group photograph of community members standing together"></div>
  <div class="abs hero-arrow" style="left:40px"><svg width="12" height="18" viewBox="0 0 12 18"><path d="M10 2L3 9l7 7" stroke="#fff" stroke-width="3" fill="none"/></svg></div>
  <div class="abs hero-arrow" style="right:40px"><svg width="12" height="18" viewBox="0 0 12 18"><path d="M2 2l7 7-7 7" stroke="#fff" stroke-width="3" fill="none"/></svg></div>
  <h1 class="abs hero-title">MARIGOLD PROJECT</h1>
  <p class="abs hero-sub">Lorem Ipsum is simply dummy</p>
</section>

<section>
  <h2 class="abs section-title" style="top:744px">About <span>Marigold</span></h2>
  <p class="abs intro" style="top:792px">Lorem Ipsum has been the industry's standard dummy text ever since the 1500s, when an unknown printer took a galley of type and scrambled it to make a type specimen book. It has survived not only five centuries, but also the leap into electronic typesetting, remaining essentially unchanged. It was popularised</p>

  <div class="abs feature" style="left:150px">
    <div class="feature-icon"><svg width="40" height="40" viewBox="0 0 24 24"><circle cx="12" cy="7" r="4" fill="#fff"/><path d="M4 21c0-5 3.5-7 8-7s8 2 8 7z" fill="#fff"/></svg></div>
    <h3>Purpose</h3>
    <p>Lorem Ipsum has been the industry's standard dummy text ever since the 1500s, when an unknown printer took a galley</p>
  </div>
  <div class="abs feature" style="left:390px">
    <div class="feature-icon"><svg width="40" height="40" viewBox="0 0 24 24"><path d="M2 11L22 3l-6 18-4-7z" fill="#fff"/></svg></div>
    <h3>Values</h3>
    <p>Lorem Ipsum has been the industry's standard dummy text ever since the 1500s, when an unknown printer took a galley</p>
  </div>
  <div class="abs feature" style="left:630px">
    <div class="feature-icon"><svg width="44" height="40" viewBox="0 0 26 24"><circle cx="13" cy="7" r="3.5" fill="#fff"/><circle cx="5" cy="9" r="2.6" fill="#fff"/><circle cx="21" cy="9" r="2.6" fill="#fff"/><path d="M7 20c0-4 2.5-7 6-7s6 3 6 7z" fill="#fff"/><path d="M1 19c0-3 1.6-5 4-5s3 1 3 1v4zM25 19c0-3-1.6-5-4-5s-3 1-3 1v4z" fill="#fff"/></svg></div>
    <h3>Meaning of Name</h3>
    <p>Lorem Ipsum has been the industry's standard dummy text ever since the 1500s, when an unknown printer took a galley</p>
  </div>
  <div class="abs feature" style="left:870px">
    <div class="feature-icon"><svg width="40" height="40" viewBox="0 0 24 24"><circle cx="12" cy="12" r="6" fill="none" stroke="#fff" stroke-width="3"/><path d="M12 2v4M12 18v4M2 12h4M18 12h4M5 5l3 3M16 16l3 3M5 19l3-3M16 8l3-3" stroke="#fff" stroke-width="2.5"/></svg></div>
    <h3>Get Started</h3>
    <p>Lorem Ipsum has been the industry's standard dummy text ever since the 1500s, when an unknown printer took a galley</p>
  </div>
</section>

<section>
  <div class="abs projects" role="img" aria-label="Dark sepia background photograph of a village scene"></div>
  <h2 class="abs section-title light" style="top:1190px">Current Projects</h2>
  <div class="abs project" style="left:96px">
    <div class="photo" role="img" aria-label="Photo of a community gathering in Cambodia"></div>
    <h4>Lotus Cambodia</h4>
    <p>Lorem Ipsum has been the industry's standard dummy text ever since the 1500s, when an unknown printer took a galley of</p>
  </div>
  <div class="abs project" style="left:440px">
    <div class="photo" role="img" aria-label="Photo of project participants in Rwanda"></div>
    <h4>Hillside Rwanda</h4>
    <p>Lorem Ipsum has been the industry's standard dummy text ever since the 1500s, when an unknown printer took a galley of</p>
  </div>
  <div class="abs project" style="left:784px">
    <div class="photo" role="img" aria-label="Photo of villagers at a project site in Kenya"></div>
    <h4>Clearwater Kenya</h4>
    <p>Lorem Ipsum has been the industry's standard dummy text ever since the 1500s, when an unknown printer took a galley of</p>
  </div>
</section>

<section>
  <h2 class="abs section-title" style="top:1640px">News <span>Stories</span></h2>
  <p class="abs intro" style="top:1690px;left:150px;width:900px">Lorem Ipsum has been the industry's standard dummy text ever since the 1500s, when an unknown printer took a galley of type and scrambled</p>
  <div class="photo video" role="img" aria-label="Video still of a story featuring women from a partner community"></div>
  <div class="abs play"><svg width="22" height="24" viewBox="0 0 22 24"><path d="M4 2l16 10L4 22z" fill="#3a2f27"/></svg></div>
  <div class="photo" style="left:612px;top:1788px;width:240px;height:164px" role="img" aria-label="Story photo of a group of people outdoors"></div>
  <div class="photo" style="left:868px;top:1788px;width:240px;height:164px" role="img" aria-label="Story photo of a rural landscape"></div>
  <h3 class="abs story-title">Simply dummy text of the printing</h3>
  <p class="abs story-text">Lorem Ipsum has been the industry's standard dummy text ever since the 1500s, when an unknown printer took a galley of type and scrambled it to make a type specimen book. It has survived not only five centuries, but also the leap into electronic typesetting, remaining unchanged.</p>
</section>

<section>
  <div class="photo give" style="left:96px;width:494px" role="img" aria-label="Sepia photo of children for the online giving banner">
    <div class="give-label">Online giving</div>
  </div>
  <div class="photo give" style="left:608px;width:504px" role="img" aria-label="Sepia photo of volunteers at work for the volunteer banner">
    <div class="give-label">Volunteer vacancies</div>
  </div>
</section>

<footer>
  <div class="abs footer"></div>
  <div class="abs footer-col" style="left:96px">
    <h5>Text Widget</h5>
    <p>Marigold helps you to quickly and easily support partner projects abroad. Give monthly, volunteer your skills and share stories with friends who care about lasting change.</p>
  </div>
  <div class="abs footer-col" style="left:380px">
    <h5>Links</h5>
    <ul><li>Customer Support</li><li>Documentation</li><li>Resources</li><li>Annual FAQs</li><li>Partnerships</li></ul>
  </div>
  <div class="abs footer-col" style="left:640px">
    <h5>Get in Touch</h5>
    <p>Address: 42 Orchard Lane,<br>Fairhaven</p>
    <p style="margin-top:8px">Phone: 555-014-2290</p>
    <p style="margin-top:8px">Email: hello@marigoldventure.org</p>
  </div>
  <div class="abs footer-col" style="left:880px">
    <h5>Newsletter</h5>
    <p>Get news and stories sent straight to your inbox.</p>
    <div class="signup"><span>Email address</span><b>Submit</b></div>
    <div class="footer-social"><i></i><i></i><i></i></div>
  </div>
  <div class="abs base">Copyright © 2015. All Rights Reserved</div>
</footer>

</body>
</html>
```